Corvana - Waste to Fuel Power Needs A Website

Make website explaining the concept and the team behind the company
Updates

I will be providing A logo and Information about the company upon signed NDA.

Coding

Coded - Design and coding required

Number of Pages Required

5+ page

```html
<!DOCTYPE html>
<html lang="en">
<head>
<meta charset="UTF-8">
<title>Corvana - Waste to Fuel Power</title>
<link href="https://fonts.googleapis.com/css2?family=League+Spartan:wght@400;500;600;700&display=swap" rel="stylesheet">
<style>
:root{
  --blue:#1a5db0;
  --green:#7cc242;
  --green-soft:#eaf5df;
  --grey-soft:#f3f3f3;
  --ink:#1b1b1b;
  --text:#3a3a3a;
  --white:#fff;
  --black:#0d0d0d;
}
*{box-sizing:border-box;margin:0;padding:0}
html,body{width:1200px;height:4471px;overflow:hidden}
body{font-family:"League Spartan",sans-serif;color:var(--text);background:var(--white);position:relative}
.btn{position:absolute;display:flex;align-items:center;justify-content:center;background:var(--green);color:#143a0c;border-radius:24px;font-size:15px;font-weight:500;text-transform:uppercase;letter-spacing:.2px}
.section-title{position:absolute;left:0;width:1200px;text-align:center;color:var(--blue);font-size:27px;font-weight:600;text-transform:uppercase}
.section-title::after{content:"";display:block;width:46px;height:3px;background:var(--green);margin:14px auto 0}

/* hero */
.hero{position:absolute;left:0;top:0;width:1200px;height:608px;background:linear-gradient(180deg,#c9d6e0 0%,#e2e8ea 35%,#b8b2a4 60%,#6f6a5c 100%)}
.brand-badge{position:absolute;left:110px;top:-80px;width:196px;height:206px;border-radius:50%;background:var(--white)}
.brand-name{position:absolute;left:136px;top:30px;font-size:32px;font-weight:700;color:var(--blue);letter-spacing:1px}
.brand-tag{position:absolute;left:138px;top:62px;font-size:8.5px;font-weight:700;color:var(--blue)}
.phone{position:absolute;left:946px;top:7px;font-size:14px;color:#222;display:flex;align-items:center;gap:8px}
.nav{position:absolute;left:304px;top:35px;width:785px;height:44px;background:var(--white);border-radius:22px;display:flex;align-items:center}
.nav a{font-size:13px;color:#111;text-decoration:none;text-transform:uppercase;margin-right:22px}
.nav .active{background:var(--blue);color:#fff;height:44px;width:70px;display:flex;align-items:center;justify-content:center;margin-left:142px;margin-right:24px}
.nav .search{position:absolute;right:10px;top:9px;width:27px;height:27px;border-radius:50%;background:var(--blue)}
.hero-title{position:absolute;left:0;width:1200px;top:180px;text-align:center;font-size:31px;font-weight:600;color:var(--ink)}
.hero-title span{color:var(--green)}
.hero-lead{position:absolute;left:220px;width:760px;top:240px;text-align:center;font-size:15px;line-height:34px;color:#222}

/* intro */
.intro-bg{position:absolute;left:0;top:608px;width:1200px;height:620px}
.eyebrow{position:absolute;left:110px;top:645px;font-size:18px;font-weight:600;color:#15324f}
.eyebrow span{color:var(--green)}
.reactor{position:absolute;left:110px;top:711px;width:486px;height:494px;border-radius:50%;border-top:6px solid var(--blue);background:radial-gradient(circle at 45% 45%,#eef0f2,#b7bcc2 60%,#7d848c)}
.intro-title{position:absolute;left:685px;top:628px;font-size:27px;font-weight:600;color:var(--blue);line-height:44px}
.intro-title::after{content:"";display:block;width:46px;height:3px;background:var(--green);margin-top:10px}
.intro-text{position:absolute;left:685px;top:758px;width:404px;font-size:15px;line-height:34.5px;text-align:justify;color:#333}

/* problem */
.card{position:absolute;background:var(--white);border:2px solid #e8e8e8;border-radius:22px;text-align:center}
.card .ico{width:80px;height:80px;border-radius:50%;background:var(--blue);margin:38px auto 0;display:flex;align-items:center;justify-content:center}
.card h3{font-size:15px;font-weight:500;color:var(--blue);margin-top:30px;text-transform:uppercase}
.card p{font-size:15px;line-height:34px;margin-top:10px;padding:0 20px}
.card.featured{background:var(--blue);border:none;color:#fff}
.card.featured .ico{background:var(--white)}
.card.featured h3{color:#fff}

/* technology */
.tech-bg{position:absolute;left:0;top:1690px;width:1200px;height:570px}
.tech-lead{position:absolute;left:0;width:1200px;top:1906px;text-align:center;font-size:15px;color:#333}
.step{position:absolute;top:1955px}
.step .num{font-size:70px;font-weight:700;color:#d8dde7;line-height:1}
.step svg{display:block;margin-top:10px}
.step .label{font-size:16px;color:#222;margin-top:22px;line-height:34px;text-transform:uppercase}
.arrow{position:absolute;top:2052px}

/* why */
.why-bg{position:absolute;left:0;top:2258px;width:1200px;height:830px}
.why-card{position:absolute;width:465px;height:198px;background:var(--white);border:2px solid #e6e6e6;border-radius:10px}
.why-card::before{content:"";position:absolute;left:-2px;top:75px;width:4px;height:48px;background:var(--green)}
.why-card svg.icon{position:absolute;left:42px;top:30px}
.why-card h3{position:absolute;left:44px;top:104px;font-size:20px;font-weight:500;color:var(--blue);text-transform:uppercase}
.why-card p{position:absolute;left:44px;top:146px;font-size:15px;color:#222}
.why-card .go{position:absolute;right:18px;bottom:18px;width:40px;height:40px;border-radius:50%;background:var(--green);display:flex;align-items:center;justify-content:center}

/* contact */
.field{position:absolute;border:1.5px solid #cfcfcf;border-radius:6px;background:var(--white);font-size:12.5px;color:#333;padding-left:16px;display:flex;align-items:center;text-transform:uppercase}
.field.area{align-items:flex-start;padding-top:22px;padding-left:22px}

/* team */
.member{position:absolute;top:3630px;width:220px}
.member .photo{width:220px;height:217px;border-radius:6px;background:linear-gradient(160deg,#dfe5ec,#b9c2cc)}
.member .name{text-align:center;font-size:17px;font-weight:500;color:#111;margin-top:28px;text-transform:uppercase}

/* footer */
.footer-bg{position:absolute;left:0;top:4050px;width:1200px;height:421px}
.partner{position:absolute;left:156px;top:4148px;font-size:27px;font-weight:600;color:#fff;text-transform:uppercase}
.foot-brand{position:absolute;left:0;width:1200px;top:4285px;text-align:center;color:#fff}
.foot-brand .n{font-size:30px;font-weight:700;letter-spacing:1px}
.foot-brand .t{font-size:8px;font-weight:700;margin-top:-2px}
.foot-nav{position:absolute;left:0;width:1200px;top:4360px;display:flex;justify-content:center;gap:24px;font-size:14px;color:#fff;text-transform:uppercase}
.copy{position:absolute;left:0;width:1200px;top:4410px;text-align:center;font-size:13px;color:#fff;text-transform:uppercase}
</style>
</head>
<body>

<!-- Hero -->
<header class="hero" role="img" aria-label="Landfill heaped with discarded plastic bottles under a cloudy sky"></header>
<div class="brand-badge"></div>
<div class="brand-name">CORVANA</div>
<div class="brand-tag">WASTE TO FUEL POWER</div>
<div class="phone">
  <svg width="13" height="13" viewBox="0 0 24 24"><path fill="#1a5db0" d="M6.6 10.8a15 15 0 006.6 6.6l2.2-2.2c.3-.3.7-.4 1-.2 1.1.4 2.3.6 3.6.6.6 0 1 .4 1 1V20c0 .6-.4 1-1 1A17 17 0 013 4c0-.6.4-1 1-1h3.5c.6 0 1 .4 1 1 0 1.3.2 2.5.6 3.6.1.3 0 .7-.2 1z"/></svg>
  123 555 0147
</div>
<nav class="nav">
  <a class="active">Home</a><a>Solution</a><a>Benefits</a><a>Industries</a><a>Our Team</a><a>Contact Us</a>
  <span class="search"><svg width="27" height="27" viewBox="0 0 27 27"><circle cx="12.5" cy="12.5" r="3.5" fill="none" stroke="#fff" stroke-width="1.4"/><path d="M15 15l3 3" stroke="#fff" stroke-width="1.4"/></svg></span>
</nav>
<h1 class="hero-title">TURNING <span>PLASTIC WASTE INTO CLEAN DIESEL</span> ENERGY</h1>
<p class="hero-lead">Corvana converts non-recyclable plastic waste into high-quality diesel fuel — reducing landfill waste while powering industry.</p>
<div class="btn" style="left:497px;top:335px;width:206px;height:42px">Contact Our Team</div>

<!-- Intro -->
<svg class="intro-bg" viewBox="0 0 1200 620" preserveAspectRatio="none"><path d="M0 0H1200V587C1120 520 1020 470 880 470C680 470 560 590 420 590C250 590 120 480 0 430Z" fill="#eaf5df"/></svg>
<div class="eyebrow">EXPERIENCE &amp; KNOW-HOW <span>SINCE 1975</span></div>
<div class="reactor" role="img" aria-label="Stainless steel plastic conversion reactor plant with pipework"></div>
<h2 class="intro-title">ADVANCED PLASTIC<br>CONVERSION TECHNOLOGY</h2>
<p class="intro-text">Corvana’s proprietary conversion process safely breaks down plastic polymers into hydrocarbon fuel.<br>The system operates in a controlled oxygen-free environment, ensuring efficient energy recovery while minimizing harmful emissions.</p>
<div class="btn" style="left:686px;top:969px;width:156px;height:42px">Learn More</div>

<!-- Problem -->
<h2 class="section-title" style="top:1281px">The Problem</h2>
<div class="card" style="left:109px;top:1346px;width:303px;height:288px">
  <div class="ico"><svg width="40" height="40" viewBox="0 0 40 40" fill="none" stroke="#fff" stroke-width="2"><rect x="8" y="12" width="11" height="22" rx="2"/><rect x="11" y="6" width="5" height="6"/><rect x="22" y="18" width="10" height="16" rx="2"/><rect x="25" y="13" width="4" height="5"/></svg></div>
  <h3>Plastic Waste Crisis</h3>
  <p>Millions of tons of plastic end up in landfills or oceans every year.</p>
</div>
<div class="card featured" style="left:448px;top:1379px;width:300px;height:286px">
  <div class="ico"><svg width="44" height="44" viewBox="0 0 44 44" fill="none" stroke="#1a5db0" stroke-width="2"><circle cx="22" cy="22" r="15"/><path d="M24 10l-8 13h7l-3 11 9-14h-7z"/></svg></div>
  <h3>Untapped Energy</h3>
  <p>Most plastic waste contains high energy potential that goes unused.</p>
</div>
<div class="card" style="left:787px;top:1346px;width:303px;height:288px">
  <div class="ico"><svg width="40" height="40" viewBox="0 0 40 40" fill="none" stroke="#fff" stroke-width="2"><circle cx="20" cy="24" r="8"/><path d="M20 4v10M12 8v8M28 8v8M17 7l3-3 3 3"/></svg></div>
  <h3>Growing Diesel Demand</h3>
  <p>Industries worldwide continue to rely on diesel for transportation.</p>
</div>

<!-- Technology -->
<svg class="tech-bg" viewBox="0 0 1200 570" preserveAspectRatio="none"><path d="M0 0C200 30 400 50 600 40C850 25 1050 0 1200 5V570H0Z" fill="#f3f3f3"/></svg>
<h2 class="section-title" style="top:1817px">Plastic to Diesel Technology</h2>
<p class="tech-lead">Corvana uses advanced thermal conversion technology to transform non-recyclable plastic into usable diesel fuel.</p>

<div class="step" style="left:109px"><div class="num">01</div>
<svg width="52" height="56" viewBox="0 0 52 56" fill="none" stroke="#1a5db0" stroke-width="2"><path d="M8 22h36l-4 30H12z"/><path d="M14 22l4-14h6l-2 14M28 22l6-16 6 2-4 14"/><path d="M22 40l4-6 4 6h-8" stroke="#7cc242"/></svg>
<div class="label">Plastic Waste</div></div>
<div class="step" style="left:372px"><div class="num">02</div>
<svg width="70" height="56" viewBox="0 0 70 56" fill="none" stroke="#1a5db0" stroke-width="2"><rect x="6" y="4" width="8" height="36" rx="4"/><circle cx="10" cy="46" r="7" stroke="#7cc242"/><path d="M26 20c4 6-4 10 0 18M36 18c4 6-4 10 0 18M46 16c4 6-4 10 0 18"/><path d="M22 50h44"/></svg>
<div class="label">Thermal Conversion<br>Reactor</div></div>
<div class="step" style="left:689px"><div class="num">03</div>
<svg width="56" height="56" viewBox="0 0 56 56" fill="none" stroke="#1a5db0" stroke-width="2"><rect x="6" y="6" width="28" height="44" rx="3"/><rect x="11" y="12" width="18" height="12"/><path d="M34 18h8l4 6v20a3 3 0 01-6 0V32h-6"/><path d="M14 40c0-6 6-8 12-8-1 6-5 9-12 8z" stroke="#7cc242"/></svg>
<div class="label">Fuel<br>Refinement</div></div>
<div class="step" style="left:919px"><div class="num">04</div>
<svg width="66" height="56" viewBox="0 0 66 56" fill="none" stroke="#1a5db0" stroke-width="2"><rect x="6" y="14" width="54" height="30" rx="4"/><path d="M14 14V8h12v6M40 14V8h12v6M12 44v6M54 44v6"/><circle cx="33" cy="29" r="8" stroke="#7cc242"/><path d="M33 23v12M27 29h12" stroke="#7cc242"/></svg>
<div class="label">Commercial Diesel<br>Output</div></div>

<svg class="arrow" style="left:243px" width="46" height="10" viewBox="0 0 46 10"><path d="M0 5h42M37 1l5 4-5 4" stroke="#111" stroke-width="1.5" fill="none"/></svg>
<svg class="arrow" style="left:528px" width="46" height="10" viewBox="0 0 46 10"><path d="M0 5h42M37 1l5 4-5 4" stroke="#111" stroke-width="1.5" fill="none"/></svg>
<svg class="arrow" style="left:802px" width="46" height="10" viewBox="0 0 46 10"><path d="M0 5h42M37 1l5 4-5 4" stroke="#111" stroke-width="1.5" fill="none"/></svg>

<!-- Why -->
<svg class="why-bg" viewBox="0 0 1200 830" preserveAspectRatio="none"><path d="M0 0H1200V640C1080 640 950 700 760 700C560 700 420 660 250 660C120 660 40 720 0 810Z" fill="#eaf5df"/></svg>
<h2 class="section-title" style="top:2317px">Why Corvana</h2>

<div class="why-card" style="left:118px;top:2410px">
  <svg class="icon" width="54" height="54" viewBox="0 0 54 54" fill="none" stroke="#1a5db0" stroke-width="2"><circle cx="30" cy="20" r="12" stroke="#7cc242"/><path d="M6 40h10l10 4 14-8M6 48h10"/></svg>
  <h3>Environmental Impact</h3>
  <p>Reduces plastic waste pollution.</p>
  <span class="go"><svg width="14" height="14" viewBox="0 0 14 14"><path d="M3 11L11 3M5 3h6v6" stroke="#fff" stroke-width="1.6" fill="none"/></svg></span>
</div>
<div class="why-card" style="left:616px;top:2449px">
  <svg class="icon" width="54" height="54" viewBox="0 0 54 54" fill="none" stroke="#1a5db0" stroke-width="2"><circle cx="27" cy="27" r="20" stroke="#7cc242"/><path d="M29 13l-9 16h8l-3 12 10-17h-8z"/></svg>
  <h3>Energy Recovery</h3>
  <p>Unlocks the energy trapped inside plastic.</p>
  <span class="go"><svg width="14" height="14" viewBox="0 0 14 14"><path d="M3 11L11 3M5 3h6v6" stroke="#fff" stroke-width="1.6" fill="none"/></svg></span>
</div>
<div class="why-card" style="left:368px;top:2683px">
  <svg class="icon" width="56" height="54" viewBox="0 0 56 54" fill="none" stroke="#1a5db0" stroke-width="2"><circle cx="28" cy="27" r="20"/><path d="M20 30c0-8 8-10 16-10-2 8-7 12-16 10z" stroke="#7cc242"/></svg>
  <h3>Circular Economy</h3>
  <p>Turns waste into valuable energy resources.</p>
  <span class="go"><svg width="14" height="14" viewBox="0 0 14 14"><path d="M3 11L11 3M5 3h6v6" stroke="#fff" stroke-width="1.6" fill="none"/></svg></span>
</div>

<!-- Contact -->
<h2 class="section-title" style="top:3108px">Contact Corvana</h2>
<div class="field" style="left:158px;top:3208px;width:422px;height:42px">Full Name</div>
<div class="field" style="left:158px;top:3273px;width:422px;height:42px">Email Address</div>
<div class="field" style="left:158px;top:3343px;width:422px;height:42px">Select Service
  <svg style="position:absolute;right:18px;top:17px" width="12" height="7" viewBox="0 0 12 7"><path d="M0 0h12L6 7z" fill="#222"/></svg></div>
<div class="field area" style="left:620px;top:3208px;width:422px;height:178px">Type Your Message</div>
<div class="btn" style="left:158px;top:3407px;width:884px;height:44px">Send Message Now</div>

<!-- Team -->
<h2 class="section-title" style="top:3532px">The Team Behind Corvana</h2>
<div class="member" style="left:123px"><div class="photo" role="img" aria-label="Portrait of team member Maren"></div><div class="name">Maren</div></div>
<div class="member" style="left:368px"><div class="photo" role="img" aria-label="Portrait of team member Tobias"></div><div class="name">Tobias</div></div>
<div class="member" style="left:612px"><div class="photo" role="img" aria-label="Portrait of team member Lena"></div><div class="name">Lena</div></div>
<div class="member" style="left:856px"><div class="photo" role="img" aria-label="Portrait of team member Elise"></div><div class="name">Elise</div></div>
<div class="btn" style="left:509px;top:3925px;width:182px;height:43px">View More Team</div>

<!-- Footer -->
<svg class="footer-bg" viewBox="0 0 1200 421" preserveAspectRatio="none"><path d="M0 60C300 20 500 0 700 10C900 20 1050 40 1200 45V421H0Z" fill="#0d0d0d"/></svg>
<div class="partner">Partner With Corvana</div>
<div class="btn" style="left:844px;top:4140px;width:198px;height:42px">Contact Our Team</div>
<div class="foot-brand"><div class="n">CORVANA</div><div class="t">WASTE TO FUEL POWER</div></div>
<div class="foot-nav"><span>Home</span><span>Solution</span><span>Benefits</span><span>Industries</span><span>Our Team</span><span>Contact Us</span></div>
<div class="copy">©2026 Copyrights - All Rights Reserved</div>

</body>
</html>
```